New Business Card for Software Company

We are looking at rebranding a 10 year old company that specializes in PDF and DWF solutions for Architects and Engineers. We will attach the new company logo that we are going with so you can work with that and complimentary colors.
The sample information we would like on the business card is:
Gerald Pinfold
Vice President
4738 W. Harrowgate Lane. STE 305
PMB#417
Mesa, AZ 85374
866-392-5074 US Toll Free
123-456-3190 Cell
gpinfold@plavorix.com
The old tag line that we had on the business cars was.
Providing Industrial Strength PDF and DWF Solutions to the Global CAD Marketplace.
If you have an idea for a better tag line we are open to that also.
Updates
We would like to thank all of the Designers for their wonderful work. We apologize that we will not have the time to provide feedback to everyone. There is just so many innovative and professional designs that you have all created making our decision even harder.
Target Market(s)
Architects and Engineers
Industry/Entity Type
Business
Look and feel

```html
<!DOCTYPE html>
<html lang="en">
<head>
<meta charset="utf-8">
<title>Plavorix Business Card</title>
<link rel="stylesheet" href="https://fonts.googleapis.com/css2?family=Open+Sans:wght@400;700;800&display=swap">
<style>
  :root {
    --bg: #e6e6ea;
    --card: #ffffff;
    --orange: #ec5a1c;
    --orange-light: #f7941d;
    --red: #c4202b;
    --grey-text: #555559;
    --dark-text: #2d2d30;
    --rule: #9a9aa0;
  }
  * { margin: 0; padding: 0; box-sizing: border-box; }
  html, body { width: 1200px; height: 987px; overflow: hidden; background: var(--bg); }
  body { font-family: "Open Sans", Arial, sans-serif; position: relative; }

  .card {
    position: absolute;
    left: 215px;
    width: 770px;
    height: 440px;
    background: var(--card);
    border-radius: 34px;
    overflow: hidden;
    box-shadow: 0 6px 18px rgba(0,0,0,0.15);
  }
  .card--front { top: 40px; }
  .card--back { top: 507px; }

  .brand {
    position: absolute;
    display: flex;
    align-items: center;
    gap: 18px;
  }
  .brand__dot {
    width: 78px; height: 78px;
    border-radius: 50%;
    background: var(--orange);
  }
  .brand__name {
    font-weight: 800;
    font-size: 96px;
    line-height: 1;
    color: var(--orange);
    letter-spacing: -2px;
  }
  .card--front .brand { left: 150px; top: 110px; }
  .tagline {
    position: absolute;
    left: 0; right: 0; top: 262px;
    text-align: center;
    text-transform: uppercase;
    color: var(--dark-text);
    font-size: 25px;
    line-height: 1.3;
    letter-spacing: 0.5px;
  }

  .card--back .brand { left: 70px; top: 44px; }
  .person {
    position: absolute;
    left: 240px; top: 158px;
    font-size: 23px;
    line-height: 1.3;
    color: var(--grey-text);
    white-space: nowrap;
  }
  .person__name { color: var(--orange); font-weight: 700; }

  .band { position: absolute; left: 0; top: 0; width: 770px; height: 440px; }
  .contact {
    position: absolute;
    color: #fff;
    font-size: 20px;
    line-height: 1.35;
    white-space: nowrap;
  }
  .contact--address { left: 120px; top: 292px; }
  .contact--lines {
    left: 40px; top: 382px;
    display: flex; align-items: center; gap: 22px;
    font-size: 19px;
  }
  .contact__item { display: flex; align-items: center; gap: 7px; }
  .contact__item svg { width: 18px; height: 18px; }
</style>
</head>
<body>

<section class="card card--front">
  <div class="brand">
    <span class="brand__dot"></span>
    <span class="brand__name">Plavorix</span>
  </div>
  <p class="tagline">Providing industrial strength PDF and<br>DWF solutions to the global CAD marketplace</p>
</section>

<section class="card card--back">
  <svg class="band" viewBox="0 0 770 440" aria-hidden="true">
    <defs>
      <radialGradient id="bandFill" cx="0.4" cy="0.65" r="0.75">
        <stop offset="0" stop-color="var(--orange-light)"/>
        <stop offset="0.55" stop-color="var(--orange)"/>
        <stop offset="1" stop-color="var(--red)"/>
      </radialGradient>
    </defs>
    <path d="M0 205 C 250 205, 550 255, 770 345" fill="none" stroke="var(--rule)" stroke-width="2"/>
    <path d="M0 215 C 250 215, 550 265, 770 355 L770 440 L0 440 Z" fill="url(#bandFill)"/>
  </svg>

  <div class="brand">
    <span class="brand__dot"></span>
    <span class="brand__name">Plavorix</span>
  </div>

  <p class="person"><span class="person__name">Gerald Pinfold,</span> Vice President</p>

  <p class="contact contact--address">4738 W. Harrowgate Lane. STE 305<br>PMB#417, Mesa, AZ 85374</p>

  <div class="contact contact--lines">
    <span class="contact__item">
      <svg viewBox="0 0 20 20"><circle cx="10" cy="10" r="9" fill="none" stroke="#fff" stroke-width="1.6"/><path d="M7 5.5 l2 2.5 -1.2 1.2 a6 6 0 0 0 3 3 l1.2-1.2 2.5 2 -1.3 1.6 C9.5 14 6 10.5 5.5 6.8Z" fill="#fff"/></svg>
      866-392-5074US(TF)
    </span>
    <span class="contact__item">
      <svg viewBox="0 0 20 20"><rect x="5.5" y="1.5" width="9" height="17" rx="1.5" fill="none" stroke="#fff" stroke-width="1.6"/><rect x="7.5" y="4" width="5" height="6" fill="#fff"/></svg>
      123-456-3190
    </span>
    <span class="contact__item">
      <svg viewBox="0 0 20 20"><rect x="2" y="5" width="16" height="11" rx="1.5" fill="none" stroke="#fff" stroke-width="1.6"/><path d="M2.5 5.5 L10 11 L17.5 5.5" fill="none" stroke="#fff" stroke-width="1.6"/></svg>
      gpinfold@plavorix.com
    </span>
  </div>
</section>

</body>
</html>
```